Stylish new business card needed!

Hello everyone! I am in need of a new business card design for an alarm company here in Hurricane WV. I have all fonts, color codes and logos provided for you use! We are a young company and like the style of a clean sleek looking business card. Would like it double sided, one side holding the logo and the other with your design!
Target Market(s)
The people that are looking for the newest tech for home automation and security
Industry/Entity Type
Alarm services; Home automation
Contact Information for Business Card
Name of person; position (Sales; Installer); Phone Number (555.418.7260); Employee cell Number; Website (www.GuardedByVelk.example); Employee Email; Double sided
Look and feel
Each slider illustrates characteristics of the customer's brand and the style your logo design should communicate.

```html
<!DOCTYPE html>
<html lang="en">
<head>
<meta charset="utf-8">
<title>Guarded by Velk – Business Card</title>
<link rel="stylesheet" href="https://fonts.googleapis.com/css2?family=Arimo:wght@400;700&display=swap">
<style>
  :root {
    --backdrop: #232323;
    --card: #1f1f23;
    --orange: #f58d4c;
    --grey: #9a9a9a;
    --white: #ffffff;
    --faint: #2c2c31;
  }
  * { margin: 0; padding: 0; box-sizing: border-box; }
  html, body {
    width: 1200px; height: 780px; overflow: hidden;
    background: var(--backdrop);
    font-family: "Arimo", Arial, sans-serif;
  }
  .stage {
    width: 1200px; height: 780px;
    display: flex; align-items: center; justify-content: center; gap: 40px;
  }
  .card {
    position: relative;
    width: 560px; height: 320px;
    background: var(--card);
    overflow: hidden;
    box-shadow: 0 10px 30px rgba(0,0,0,.45);
  }

  /* Front */
  .front { display: flex; align-items: center; justify-content: center; }
  .brand-name {
    color: var(--orange);
    font-weight: 700;
    text-transform: uppercase;
    letter-spacing: 1px;
  }
  .front .brand-name { font-size: 48px; }

  /* Back */
  .back-watermark {
    position: absolute;
    left: -92px; top: 150px;
    transform: rotate(90deg);
    transform-origin: center;
    font-size: 130px; font-weight: 700;
    color: var(--faint);
    letter-spacing: 6px;
    line-height: 1;
  }
  .back-brand {
    position: absolute; right: 36px; top: 40px;
    font-size: 22px;
  }
  .person {
    position: absolute; right: 36px; top: 108px;
    display: flex; align-items: stretch; gap: 10px;
  }
  .person-text { text-align: right; }
  .person-name { font-size: 26px; font-weight: 700; line-height: 1.05; }
  .first-name { color: var(--orange); }
  .last-name { color: var(--grey); }
  .person-role { color: var(--white); font-size: 14px; font-weight: 700; margin-top: 4px; }
  .accent-bar { width: 10px; background: var(--orange); }
  .contacts {
    position: absolute; right: 36px; top: 196px;
    list-style: none;
  }
  .contacts li {
    display: flex; align-items: center; justify-content: flex-end; gap: 10px;
    color: var(--white); font-size: 14px; line-height: 22px;
  }
  .contacts svg { width: 14px; height: 14px; fill: var(--orange); flex: none; }
</style>
</head>
<body>
<main class="stage">
  <section class="card front">
    <div class="brand-name">Guarded by Velk</div>
  </section>

  <section class="card back">
    <div class="back-watermark" aria-hidden="true">VELK</div>
    <div class="brand-name back-brand">Guarded by Velk</div>

    <div class="person">
      <div class="person-text">
        <div class="person-name"><span class="first-name">Marta</span> <span class="last-name">Kovalenko</span></div>
        <div class="person-role">Sales; Installer</div>
      </div>
      <div class="accent-bar"></div>
    </div>

    <ul class="contacts">
      <li>555.418.7260
        <svg viewBox="0 0 24 24" aria-hidden="true"><path d="M6.6 10.8a15 15 0 0 0 6.6 6.6l2.2-2.2a1 1 0 0 1 1-.25 11.4 11.4 0 0 0 3.6.57 1 1 0 0 1 1 1V20a1 1 0 0 1-1 1A17 17 0 0 1 3 4a1 1 0 0 1 1-1h3.5a1 1 0 0 1 1 1c0 1.25.2 2.45.57 3.57a1 1 0 0 1-.25 1z"/></svg>
      </li>
      <li>555.902.3318
        <svg viewBox="0 0 24 24" aria-hidden="true"><path d="M7 2h10a2 2 0 0 1 2 2v16a2 2 0 0 1-2 2H7a2 2 0 0 1-2-2V4a2 2 0 0 1 2-2zm0 3v13h10V5zm5 14.2a1 1 0 1 0 0 .01z"/></svg>
      </li>
      <li>www.GuardedByVelk.example
        <svg viewBox="0 0 24 24" aria-hidden="true"><path d="M12 2a10 10 0 1 0 0 20 10 10 0 0 0 0-20zm6.9 6h-3a15 15 0 0 0-1.3-3.9A8 8 0 0 1 18.9 8zM12 4c.8 1.2 1.5 2.5 1.9 4h-3.8c.4-1.5 1.1-2.8 1.9-4zM4.3 14a8 8 0 0 1 0-4h3.4a16 16 0 0 0 0 4zm.8 2h3a15 15 0 0 0 1.3 3.9A8 8 0 0 1 5.1 16zm3-8h-3a8 8 0 0 1 4.3-3.9A15 15 0 0 0 8.1 8zM12 20c-.8-1.2-1.5-2.5-1.9-4h3.8c-.4 1.5-1.1 2.8-1.9 4zm2.3-6H9.7a14 14 0 0 1 0-4h4.6a14 14 0 0 1 0 4zm.3 5.9a15 15 0 0 0 1.3-3.9h3a8 8 0 0 1-4.3 3.9zm1.7-5.9a16 16 0 0 0 0-4h3.4a8 8 0 0 1 0 4z"/></svg>
      </li>
      <li>info@GuardedByVelk.example
        <svg viewBox="0 0 24 24" aria-hidden="true"><path d="M3 5h18a1 1 0 0 1 1 1v12a1 1 0 0 1-1 1H3a1 1 0 0 1-1-1V6a1 1 0 0 1 1-1zm1 2.4V17h16V7.4l-8 5.3z"/></svg>
      </li>
    </ul>
  </section>
</main>
</body>
</html>
```